New business card for a regional office of a US M&A company

We need business card for a finance company, office based in Hong Kong , our Head office is in US, our business is to Merge and acquires companies , the new office will be a regional office for the Asia Pacific region. We want to use the head office logo as attached ( but don't have to be exactly the same, can be a variation to it) as a base and then add Asia Pacific alongside the logo.
We would prefer to have be bilingual Eng + Chinese, although we don't really have Chinese company name .

Industry/Entity Type

Business

Contact Information for Business Card

Clara Jo Tsang
 

VP,
APAC M&A Operations
Orin Vantage Asia Pacific Limited
 
Unit 1407, K18
18 Tai Lok Shan Road, 
Hong Kong 
 
M: +852 6038 1742
T : +852 2836 4100
F : +852 2836 4177
VOIP: 4158
 
cjtsang@orinvantage.com

Font styles to use
Serif
Sans Serif

Colors

Designer to choose colors to be used in the design.

Requirements
Must have
• APAC Office

```html
<!DOCTYPE html>
<html lang="en">
<head>
<meta charset="utf-8">
<title>Orin Vantage – APAC Business Card</title>
<link href="https://fonts.googleapis.com/css2?family=Open+Sans:wght@700&family=Roboto:wght@400&family=Roboto+Condensed:wght@700&display=swap" rel="stylesheet">
<style>
  :root {
    --backdrop: #2a2a2a;
    --navy: #10283f;
    --navy-faint: #1c3a55;
    --sky: #21aed4;
    --ink-dark: #122b45;
    --paper: #ffffff;
    --soft-white: #e9f6fb;
  }
  * { margin: 0; padding: 0; box-sizing: border-box; }
  html, body { width: 1200px; height: 960px; overflow: hidden; }
  body {
    position: relative;
    background: var(--backdrop);
    font-family: "Roboto", Arial, sans-serif;
  }
  .card {
    position: absolute;
    left: 320px;
    width: 600px;
    height: 343px;
    overflow: hidden;
  }

  /* Back of card */
  .card-back { top: 108px; background: var(--navy); }
  .card-back .decor-circle {
    position: absolute;
    left: 30px; top: 20px;
    width: 300px; height: 300px;
    border-radius: 50%;
    border: 46px solid var(--navy-faint);
  }
  .card-back .brand {
    position: absolute;
    right: 30px; top: 246px;
    font-family: "Open Sans", Arial, sans-serif;
    font-weight: 700;
    font-size: 44px;
    line-height: 1;
    color: var(--sky);
    letter-spacing: -0.5px;
  }
  .card-back .web {
    position: absolute;
    right: 30px; top: 296px;
    font-size: 14px;
    color: var(--paper);
    letter-spacing: 5.5px;
  }

  /* Front of card */
  .card-front { top: 492px; background: var(--navy); }
  .contact-panel {
    position: absolute;
    left: 0; top: 0;
    width: 290px; height: 343px;
    background: var(--sky);
  }
  .divider { position: absolute; left: 276px; top: 0; }
  .person-name {
    position: absolute;
    left: 34px; top: 25px;
    font-family: "Roboto Condensed", Arial, sans-serif;
    font-weight: 700;
    font-size: 21px;
    color: var(--ink-dark);
  }
  .person-title {
    position: absolute;
    left: 36px; top: 51px;
    font-family: "Roboto Condensed", Arial, sans-serif;
    font-weight: 700;
    font-size: 14px;
    color: var(--paper);
  }
  .address {
    position: absolute;
    left: 35px; top: 125px;
    font-size: 14px;
    line-height: 19px;
    color: var(--soft-white);
    font-style: normal;
  }
  .phones {
    position: absolute;
    left: 35px; top: 225px;
    list-style: none;
    font-size: 14px;
    line-height: 19px;
    color: var(--soft-white);
  }
  .phones li { display: flex; align-items: center; gap: 8px; }
  .phones svg { width: 15px; height: 15px; fill: var(--ink-dark); }
  .voip {
    position: absolute;
    left: 35px; top: 292px;
    font-size: 14px;
    color: var(--soft-white);
  }
  .brand-block {
    position: absolute;
    left: 290px; top: 112px;
    width: 310px;
    display: flex;
    flex-direction: column;
    align-items: center;
    gap: 18px;
  }
  .brand-square { width: 40px; height: 40px; background: var(--paper); }
  .brand-block .brand {
    font-family: "Open Sans", Arial, sans-serif;
    font-weight: 700;
    font-size: 36px;
    line-height: 1;
    color: var(--sky);
    letter-spacing: -0.5px;
  }
</style>
</head>
<body>

  <section class="card card-back">
    <div class="decor-circle" aria-hidden="true"></div>
    <div class="brand">ORIN VANTAGE</div>
    <div class="web">www.orinvantage.com</div>
  </section>

  <section class="card card-front">
    <div class="contact-panel">
      <h1 class="person-name">CLARA JO TSANG</h1>
      <p class="person-title">VP</p>
      <address class="address">
        APAC M&amp;A Operations<br>
        Orin Vantage Asia Pacific Limited<br>
        Unit 1407, K18<br>
        18 Tai Lok Shan Road<br>
        Hong Kong
      </address>
      <ul class="phones">
        <li>
          <svg viewBox="0 0 16 16" aria-label="Telephone"><path d="M3 1l3 3-1.5 2a9 9 0 0 0 5.5 5.5L12 10l3 3-2 2C7 15 1 9 1 3z"/></svg>
          +852 2836 4100
        </li>
        <li>
          <svg viewBox="0 0 16 16" aria-label="Mobile"><path d="M4 0h8v16H4zM5.5 2v10h5V2zM7 13h2v2H7z" fill-rule="evenodd"/></svg>
          +852 6038 1742
        </li>
        <li>
          <svg viewBox="0 0 16 16" aria-label="Fax"><path d="M4 1h8v4H4zM1 6h14v6H1zM4 10h8v5H4z"/></svg>
          +852 2836 4177
        </li>
      </ul>
      <p class="voip">VOIP: 4158</p>
    </div>

    <svg class="divider" width="24" height="343" viewBox="0 0 24 343" aria-hidden="true">
      <polyline points="14,0 14,30 4,46 14,62 14,343" fill="none" stroke="#ffffff" stroke-width="2.5"/>
    </svg>

    <div class="brand-block">
      <div class="brand-square" aria-hidden="true"></div>
      <div class="brand">ORIN VANTAGE</div>
    </div>
  </section>

</body>
</html>
```